Steadfast Corner Vending Needs a Promotional Flyer

Design a one page, one sided 8 1/2" x 11" flyer that can be handed out to potential customers. Please keep printing efficiencies in mind. See attached old flyers and company website (steadfastcornervend.example) for reference of services. I have also attached our current logo.

```html
<!DOCTYPE html>
<html lang="en">
<head>
<meta charset="utf-8">
<title>Steadfast Corner Vending – Flyer</title>
<link rel="stylesheet" href="https://fonts.googleapis.com/css2?family=Poppins:wght@400;500;600;700;800&display=swap">
<style>
:root{
  --navy:#14293a;
  --blue:#1592cf;
  --white:#ffffff;
  --stage:#e9eaec;
  --coffee:#6b4a33;
  --shelf:#7a5a3e;
}
*{box-sizing:border-box;margin:0;padding:0}
html,body{width:1200px;height:2616px;overflow:hidden;background:var(--stage);font-family:'Poppins',sans-serif;color:var(--navy)}
.flyer{position:absolute;left:50px;top:598px;width:968px;height:1250px;background:var(--white);transform:scale(1.1364);transform-origin:0 0;overflow:hidden;box-shadow:0 6px 24px rgba(0,0,0,.18)}
.abs{position:absolute}
.hero-band{left:571px;top:0;width:397px;height:487px;background:var(--blue)}
.hero-ornament{left:838px;top:22px;width:100px;height:200px;background:var(--navy)}
.brand{left:108px;top:96px;display:flex;align-items:center;gap:12px}
.brand-mark{width:30px;height:30px;background:var(--navy)}
.brand-name{font-weight:700;font-size:26px;color:var(--navy);line-height:1.05;width:260px}
.headline{left:83px;top:218px;font-weight:800;line-height:1.02;letter-spacing:-.5px}
.headline .lead{display:block;font-size:45px;color:var(--navy)}
.headline .accent{display:block;font-size:72px;color:var(--blue);line-height:.98}
.machines{left:520px;top:150px;width:405px;height:333px;background:linear-gradient(90deg,#2e3238 0 44%,#d9322a 44% 100%);border-radius:4px}
.badge{left:640px;top:36px;width:106px;height:106px;border-radius:50%;background:var(--navy);display:flex;align-items:center;justify-content:center}
.badge-inner{width:84px;height:84px;border-radius:50%;background:var(--white);display:flex;flex-direction:column;align-items:center;justify-content:center;line-height:1}
.badge-inner .num{font-weight:800;font-size:26px;color:var(--navy)}
.badge-inner .yr{font-weight:700;font-size:13px;color:var(--blue)}
.badge-inner .exp{font-weight:600;font-size:7px;letter-spacing:.5px;color:var(--navy)}
.why{left:48px;top:495px;width:855px;height:208px;background:var(--navy);color:var(--white);padding:14px 34px}
.why h2{font-weight:400;font-size:23px}
.why h2 span{font-weight:700;color:var(--blue)}
.why-grid{position:relative;margin-top:10px;height:150px}
.point{position:absolute;display:flex;gap:14px;font-size:13px;line-height:1.2;align-items:flex-start}
.point svg{flex:none;width:28px;height:28px}
.section-title{left:80px;top:732px;font-weight:800;font-size:30px;letter-spacing:-.3px}
.label{background:var(--blue);color:var(--white);font-weight:700;font-size:20px;line-height:1;padding:2px 10px;text-transform:uppercase}
.list{list-style:none;font-size:12.5px;font-weight:600;line-height:1.28}
.list li{padding-left:14px;position:relative}
.list li::before{content:"";position:absolute;left:2px;top:5px;width:6px;height:6px;border-radius:50%;border:2px solid var(--blue)}
.ticks{list-style:none;font-size:12px;font-weight:400;line-height:1.22;margin-left:14px}
.ticks li::before{content:"✓ ";font-size:10px}
.cols{display:flex;gap:14px}
.photo-coffee{left:305px;top:775px;width:150px;height:110px;background:radial-gradient(circle at 45% 50%,#f3efe9 0 30%,var(--coffee) 60%,#3b2718)}
.photo-vend{left:305px;top:1016px;width:150px;height:110px;background:linear-gradient(90deg,#2b2f35,#4b5058 70%,#2b2f35)}
.photo-pantry{left:735px;top:775px;width:150px;height:110px;background:linear-gradient(90deg,var(--shelf),#b08863 50%,#d9dde0)}
.photo-market{left:735px;top:956px;width:150px;height:112px;background:linear-gradient(90deg,#8a6a48,#c9a878 45%,#a33 80%,#3c6fb0)}
.footer{left:0;top:1156px;width:968px;height:94px}
.call{left:88px;top:1166px;color:var(--white);font-weight:600;font-size:19px;line-height:1.2}
.call .phone{display:flex;align-items:center;gap:6px;font-size:30px;font-weight:500}
.contact{display:flex;align-items:center;gap:8px;font-size:15px;line-height:1.15;color:var(--navy)}
</style>
</head>
<body>
<main class="flyer">
  <div class="abs hero-band"></div>
  <div class="abs hero-ornament" role="img" aria-label="Decorative open-door graphic in navy and white"></div>

  <div class="abs brand"><span class="brand-mark"></span><span class="brand-name">Steadfast Corner Vending</span></div>

  <h1 class="abs headline">
    <span class="lead">WELCOME</span>
    <span class="lead">TO STEADFAST</span>
    <span class="accent">CORNER</span>
    <span class="accent">VENDING</span>
  </h1>

  <div class="abs machines" role="img" aria-label="Photo of a snack vending machine beside a red cold-drink vending machine"></div>

  <div class="abs badge"><div class="badge-inner"><span class="exp">★ ★ ★</span><span class="num">35</span><span class="yr">YEAR</span><span class="exp">EXPERIENCE</span></div></div>

  <section class="abs why">
    <h2>Why Choose Our <span>Vending Machine Services?</span></h2>
    <div class="why-grid">
      <div class="point" style="left:0;top:0;width:260px"><svg viewBox="0 0 28 28"><circle cx="14" cy="14" r="12" fill="none" stroke="var(--blue)" stroke-width="2"/><path d="M15 7l-5 8h4l-1 6 5-8h-4z" fill="var(--white)"/></svg><span>Our warehouse is just minutes away so we can get there quickly if a problem should arise.</span></div>
      <div class="point" style="left:0;top:60px;width:260px"><svg viewBox="0 0 28 28"><circle cx="14" cy="14" r="12" fill="none" stroke="var(--blue)" stroke-width="2"/><rect x="10" y="8" width="8" height="12" fill="none" stroke="var(--white)" stroke-width="1.5"/></svg><span>We are a small company that is BIG on service.</span></div>
      <div class="point" style="left:0;top:105px;width:260px"><svg viewBox="0 0 28 28"><circle cx="14" cy="14" r="12" fill="none" stroke="var(--blue)" stroke-width="2"/><circle cx="14" cy="11" r="3" fill="var(--white)"/><path d="M8 20c1-4 11-4 12 0z" fill="var(--white)"/></svg><span>Customer Service is our priority.</span></div>
      <div class="point" style="left:292px;top:0;width:230px"><svg viewBox="0 0 28 28"><circle cx="14" cy="14" r="12" fill="var(--blue)"/><path d="M9 15l4 3 6-7" fill="none" stroke="var(--white)" stroke-width="2"/></svg><span>We are Owner-Operators so we truly CARE about our customers.</span></div>
      <div class="point" style="left:292px;top:62px;width:230px"><svg viewBox="0 0 28 28"><circle cx="14" cy="14" r="12" fill="var(--blue)"/><circle cx="14" cy="12" r="4" fill="none" stroke="var(--white)" stroke-width="2"/><path d="M11 16l-1 5 4-2 4 2-1-5" fill="var(--white)"/></svg><span>We are also trained to fix many problems on the spot.</span></div>
      <div class="point" style="left:550px;top:0;width:240px"><svg viewBox="0 0 28 28"><circle cx="14" cy="14" r="12" fill="var(--blue)"/><path d="M8 15c2 4 10 4 12 0" fill="none" stroke="var(--white)" stroke-width="2"/><circle cx="14" cy="10" r="2.5" fill="var(--white)"/></svg><span>We will supply machines to your facility.</span></div>
      <div class="point" style="left:550px;top:48px;width:240px"><svg viewBox="0 0 28 28"><circle cx="14" cy="14" r="12" fill="var(--blue)"/><rect x="8" y="10" width="3" height="9" fill="var(--white)"/><rect x="12.5" y="8" width="3" height="11" fill="var(--white)"/><rect x="17" y="11" width="3" height="8" fill="var(--white)"/></svg><span>Your employees can choose what types of snacks and drinks they would like to see in the machines.</span></div>
    </div>
  </section>

  <h2 class="abs section-title">STEADFAST SUPERIOR SERVICE</h2>

  <div class="abs" style="left:81px;top:775px;width:215px">
    <div class="label">Coffee Service</div>
    <ul class="list" style="margin-top:5px"><li>Reliability</li><li>Our Coffee Selection</li></ul>
    <div class="cols"><ul class="ticks"><li>Harborline Roast</li><li>Morning Ring</li><li>Polar Crest</li><li>Mapleton House</li></ul><ul class="ticks" style="margin-left:0"><li>Elkridge</li><li>Stillwater</li><li>Fieldgate</li></ul></div>
  </div>
  <div class="abs photo-coffee" role="img" aria-label="Photo of a cup of coffee surrounded by coffee beans"></div>
  <div class="abs" style="left:81px;top:904px;width:380px">
    <ul class="list"><li>Tea and other Tasty Hot Beverages</li><li>Coffee Accessories</li></ul>
    <div class="cols" style="gap:12px"><ul class="ticks"><li>Coffee Pots</li><li>Filters</li><li>Cups</li><li>Stirrers</li></ul><ul class="ticks" style="margin-left:0"><li>Sleeves</li><li>Napkins</li><li>Sugar</li><li>Sweet-n-Lite</li></ul><ul class="ticks" style="margin-left:0;margin-top:2px"><li>Evenly</li><li>Liquid Creamers</li><li>flavored and regular</li></ul></div>
  </div>

  <div class="abs" style="left:81px;top:1016px;width:215px">
    <div class="label" style="padding:3px 8px;line-height:.95">Vending Machine<br>Services</div>
    <ul class="list" style="margin-top:8px"><li>Discover Reliability,</li><li>Variety At Zero Cost to You</li><li>Convenience</li><li>Quality</li></ul>
  </div>
  <div class="abs photo-vend" role="img" aria-label="Photo of a stocked snack vending machine"></div>

  <div class="abs" style="left:505px;top:775px;width:220px">
    <div class="label">Pantry Service</div>
    <ul class="list" style="margin-top:6px"><li>A Snack Time Oasis in Your Workspace</li><li>Tailored to Your Tastes</li><li>Healthy Choices, Happy Teams</li><li>Seamless Restocking and Management</li><li>Flexible and Hassle-Free</li><li>Enhancing Workplace Culture</li></ul>
  </div>
  <div class="abs photo-pantry" role="img" aria-label="Photo of an office pantry with stocked shelves and a drinks cooler"></div>

  <div class="abs" style="left:505px;top:958px;width:220px">
    <div class="label">Micro-Market</div>
    <ul class="list" style="margin-top:6px"><li>Experience Unmatched Convenience</li><li>Tailored to Your Taste</li><li>Seamless and Secure Transactions</li><li>Freshness Guaranteed</li><li>Smart Inventory Management</li><li>Promoting Workplace Wellbeing</li></ul>
  </div>
  <div class="abs photo-market" role="img" aria-label="Photo of micro-market shelves stocked with snacks"></div>

  <svg class="abs footer" viewBox="0 0 968 94" aria-hidden="true">
    <polygon points="0,0 363,0 398,94 0,94" fill="var(--navy)"/>
    <polygon points="370,0 382,0 417,94 405,94" fill="var(--blue)"/>
    <rect x="410" y="88" width="558" height="6" fill="var(--blue)"/>
  </svg>
  <div class="abs call">CALL US AT
    <div class="phone"><svg width="22" height="22" viewBox="0 0 24 24" aria-hidden="true"><path d="M6.6 10.8a15 15 0 0 0 6.6 6.6l2.2-2.2c.3-.3.7-.4 1-.2 1.1.4 2.3.6 3.6.6.6 0 1 .4 1 1V20c0 .6-.4 1-1 1A17 17 0 0 1 3 4c0-.6.4-1 1-1h3.5c.6 0 1 .4 1 1 0 1.3.2 2.5.6 3.6.1.3 0 .7-.2 1z" fill="var(--blue)"/></svg>555-014-2290</div>
  </div>
  <div class="abs contact" style="left:405px;top:1185px"><svg width="18" height="22" viewBox="0 0 18 22" aria-hidden="true"><path d="M9 1a7 7 0 0 0-7 7c0 5 7 12 7 12s7-7 7-12a7 7 0 0 0-7-7z" fill="none" stroke="var(--blue)" stroke-width="2"/><circle cx="9" cy="8" r="2.5" fill="var(--blue)"/></svg><span>1480 Larkspur Ave, Unit 210,<br>Fairbrook, IL 60000</span></div>
  <div class="abs contact" style="left:672px;top:1186px"><svg width="18" height="18" viewBox="0 0 18 18" aria-hidden="true"><circle cx="9" cy="9" r="7.5" fill="none" stroke="var(--blue)" stroke-width="1.6"/><ellipse cx="9" cy="9" rx="3.2" ry="7.5" fill="none" stroke="var(--blue)" stroke-width="1.4"/><path d="M1.5 9h15" stroke="var(--blue)" stroke-width="1.4"/></svg><span>steadfastcornervend.example</span></div>
</main>
</body>
</html>
```